BOLD & MINIMALIST DESIGN NEEDED

We want a very bold but minimalistic business card design that is impactful and utilizes both sides of the business card. Our current logo is included for your use.

We want bold fonts and good use of negative space. We don't want the logo to overpower the design.

Target Market(s)

Professionals who are building new commercial buildings.

Industry/Entity Type

Construction

Contact Information for Business Card

Name, Title, email, office phone, cell phone, website

Font styles to use
Serif
Sans Serif

Requirements
Must have
• Bold design!

```html
<!DOCTYPE html>
<html lang="en">
<head>
<meta charset="utf-8">
<title>Ridgeline Business Card</title>
<link rel="stylesheet" href="https://fonts.googleapis.com/css2?family=Archivo:wght@400;800;900&display=swap">
<style>
  :root {
    --canvas: #e4e4e4;
    --card-light: #f7f7f6;
    --card-dark: #3a3a3a;
    --ink: #111111;
    --ink-soft: #3c3c3c;
    --green: #79c62b;
    --green-light: #a6dc6a;
    --white: #ffffff;
  }
  * { margin: 0; padding: 0; box-sizing: border-box; }
  html, body {
    width: 1200px; height: 1200px; overflow: hidden;
    background: var(--canvas);
    font-family: "Archivo", Arial, sans-serif;
  }
  .canvas { position: relative; width: 1200px; height: 1200px; }
  .card {
    position: absolute; left: 262px; width: 690px; height: 395px;
    border-radius: 18px; overflow: hidden;
  }
  .card-front { top: 160px; background: var(--card-light); }
  .card-back { top: 650px; background: var(--card-dark);
    display: flex; align-items: center; justify-content: center; }

  .wordmark {
    display: flex; align-items: center; gap: 12px;
    font-weight: 900; letter-spacing: 0.5px; line-height: 1;
  }
  .wordmark-square { width: 0.62em; height: 0.62em; background: var(--green); }
  .card-front .wordmark {
    position: absolute; left: 42px; top: 82px;
    font-size: 44px; color: var(--ink);
  }
  .card-back .wordmark { font-size: 58px; color: var(--white); }

  .holder { position: absolute; left: 42px; top: 203px; }
  .holder-name { font-weight: 800; font-size: 25px; color: var(--ink); letter-spacing: 0.3px; }
  .holder-title { font-size: 16px; color: var(--green); margin-top: 6px; }
  .holder-rule { width: 25px; height: 1.5px; background: var(--green); margin-top: 18px; }

  .contacts { position: absolute; left: 42px; top: 290px; list-style: none; }
  .contacts li {
    display: flex; align-items: center; gap: 12px;
    font-size: 16px; color: var(--ink-soft); height: 20.5px;
  }
  .contacts svg { width: 13px; height: 13px; fill: var(--ink); flex: none; }

  .brand-field {
    position: absolute; left: 308px; top: 90px; width: 382px; height: 305px;
    background: linear-gradient(90deg, var(--ink) 0 50%, var(--green) 50% 100%);
    clip-path: polygon(0 30%, 18% 30%, 18% 0, 100% 0, 100% 100%, 0 100%);
    opacity: 0.95;
  }
</style>
</head>
<body>
<div class="canvas">
  <section class="card card-front">
    <div class="wordmark"><span class="wordmark-square"></span>RIDGELINE</div>

    <div class="holder">
      <p class="holder-name">DANIEL BROOKS</p>
      <p class="holder-title">President</p>
      <div class="holder-rule"></div>
    </div>

    <ul class="contacts">
      <li><svg viewBox="0 0 16 16"><path d="M3.5 1l2.6 3-1.5 1.8c.9 2 2.6 3.7 4.6 4.6l1.8-1.5 3 2.6-1.7 2.5C6.7 13.8 2.2 9.3 1 3.2z"/></svg>555-210-4870</li>
      <li><svg viewBox="0 0 16 16"><path d="M4 0h8a1 1 0 0 1 1 1v14a1 1 0 0 1-1 1H4a1 1 0 0 1-1-1V1a1 1 0 0 1 1-1zm.6 1.8v10.6h6.8V1.8z"/></svg>555-382-9164</li>
      <li><svg viewBox="0 0 16 16"><path d="M0 3h16v10H0zm1.5 1.4v.4L8 9l6.5-4.2v-.4zm0 2.2v5h13v-5L8 10.8z"/></svg>info@ridgelinebuild.com</li>
      <li><svg viewBox="0 0 16 16"><path d="M8 0a8 8 0 1 1 0 16A8 8 0 0 1 8 0zm-2 3.5L3 5.5l1.5 3 2.5.5-.5 3 2 1.5.5-3 2-1.5-1.5-2L7 6.5z"/></svg>www.ridgelinebuild.com</li>
    </ul>

    <div class="brand-field" role="img" aria-label="Large brand decoration area in black and green"></div>
  </section>

  <section class="card card-back">
    <div class="wordmark"><span class="wordmark-square"></span>RIDGELINE</div>
  </section>
</div>
</body>
</html>
```